Mastering Modern Vineyard Management

size of the ad - 8”x 10.75" plus 0.25" bleed
I would like an ad for a magazine that will stand out and make people want to read the ad.
The ad should not be crowded and people reading the ad will be able to read the text.
I would like it to be a creative and modern-day design.
the list of topics should not be the focus of the ad.
the text is attached.
If you decide to use people in the ad then please no ladies.
please note that leave over 1 inch for the bottom of the footer

```html
<!DOCTYPE html>
<html lang="en">
<head>
<meta charset="utf-8">
<title>Vine Grower Course – Magazine Ad</title>
<link href="https://fonts.googleapis.com/css2?family=Antonio:wght@200;700&family=Poppins:wght@300;400;500;600;700;800&family=Oswald:wght@500&display=swap" rel="stylesheet">
<style>
  :root{
    --navy:#14233e;
    --navy-deep:#0d1a30;
    --ink:#111a26;
    --blue:#4a9bef;
    --blue-box:#4f9ff0;
    --green:#2fae4a;
    --white:#ffffff;
    --backdrop:#e2e2e2;
    --skin:#b59a7c;
  }
  *{margin:0;padding:0;box-sizing:border-box}
  html,body{width:1200px;height:2550px;overflow:hidden}
  body{background:var(--backdrop);position:relative;font-family:"Poppins",sans-serif;color:var(--ink)}
  .ad{position:absolute;left:60px;top:556px;width:1080px;height:1437px;background:var(--white);overflow:hidden;box-shadow:0 18px 40px rgba(0,0,0,.28)}
  .abs{position:absolute}
  .skyline{left:0;top:0;width:1080px;height:620px;background:linear-gradient(180deg,var(--navy-deep) 0%,#1c3255 55%,#22395e 100%)}
  .tear{left:0;top:470px;width:1080px;height:160px}
  .portrait{left:540px;top:79px;width:540px;height:546px;background:linear-gradient(180deg,#3a4a63 0%,var(--skin) 45%,#8a7660 100%);clip-path:polygon(32% 0,68% 0,72% 28%,95% 40%,100% 100%,0 100%,6% 42%,30% 28%)}
  .headline{left:97px;top:88px;font-family:"Antonio",sans-serif;font-size:146px;line-height:137px;color:var(--white);font-weight:700;letter-spacing:-1px}
  .headline .light{color:var(--blue);font-weight:200}
  .course-name{left:97px;top:624px;font-size:34px;line-height:34px;text-transform:uppercase}
  .course-name .lead{color:var(--blue);font-weight:700}
  .course-name .rest{font-weight:400;color:var(--ink)}
  .topics-title{left:97px;top:716px;font-size:68px;font-weight:800;line-height:72px;color:var(--ink)}
  .topics-sub{left:99px;top:790px;font-size:27px;letter-spacing:6px;color:var(--blue);font-weight:500}
  .topics{left:99px;top:862px;list-style:none;font-size:24px;font-weight:500;line-height:41px}
  .topics li{display:flex;align-items:center;gap:10px}
  .topics svg{width:19px;height:19px;flex:none}
  .tagline{left:605px;top:622px;width:475px;height:64px;background:var(--navy-deep);border-radius:10px 0 0 10px;padding:8px 0 0 22px;font-size:23px;line-height:23px;color:var(--white)}
  .tagline b{color:var(--blue);font-weight:700;display:block}
  .location{left:605px;top:718px;width:380px;display:flex;align-items:center;gap:14px;font-size:36px;font-weight:400}
  .location::before,.location::after{content:"";flex:1;height:2px;background:var(--blue)}
  .box{left:605px;width:380px;background:var(--blue-box);border-radius:10px}
  .schedule{top:780px;height:225px}
  .early{top:1027px;height:224px}
  .day{left:28px;top:20px;font-size:46px;font-weight:800;color:var(--white);line-height:56px;white-space:nowrap}
  .small-cap{font-family:"Oswald",sans-serif;font-size:15px;letter-spacing:.3px;color:var(--ink)}
  .scholar{left:30px;top:98px}
  .evenings{left:28px;top:114px;font-size:46px;line-height:44px;font-weight:800;color:var(--ink)}
  .evenings span{display:block;color:var(--white);font-weight:300}
  .divider{left:272px;top:100px;width:2px;height:98px;background:var(--ink)}
  .starting{left:284px;top:96px}
  .date{left:282px;top:108px;font-weight:800;line-height:48px}
  .date .month{font-size:40px;color:var(--white);display:block}
  .date .num{font-size:60px;color:var(--ink);display:block;line-height:54px}
  .early-title{left:30px;top:54px;font-size:44px;line-height:42px;font-weight:800;color:var(--ink)}
  .early-title span{display:block;color:var(--white);font-weight:300}
  .early-note{left:212px;top:58px;font-size:21px;line-height:23px;font-weight:500;color:var(--ink)}
</style>
</head>
<body>
<main class="ad">
  <div class="abs skyline" role="img" aria-label="Rows of vineyard hills at dusk in deep navy tones"></div>
  <svg class="abs tear" viewBox="0 0 1080 160" preserveAspectRatio="none" aria-hidden="true">
    <path fill="#ffffff" d="M0 118 L40 104 L70 120 L110 96 L150 112 L190 88 L230 104 L268 80 L300 96 L340 70 L380 90 L420 62 L455 84 L490 56 L530 70 L560 40 L600 58 L640 36 L680 52 L720 30 L760 48 L800 26 L840 40 L880 20 L920 34 L960 14 L1000 30 L1040 10 L1080 22 L1080 160 L0 160 Z"/>
    <circle cx="120" cy="84" r="6" fill="#ffffff"/><circle cx="260" cy="64" r="5" fill="#ffffff"/><circle cx="430" cy="44" r="7" fill="#ffffff"/>
  </svg>
  <div class="abs portrait" role="img" aria-label="Presenter in a tan blazer giving a thumbs up and holding a small bunch of grapes"></div>

  <h1 class="abs headline">VINE<br>GROWER<br><span class="light">COURSE</span></h1>

  <p class="abs course-name"><span class="lead">Mastering Modern</span><br><span class="rest">Vineyard Management</span></p>

  <h2 class="abs topics-title">TOPICS</h2>
  <p class="abs topics-sub">PARTIAL LISTING</p>
  <ul class="abs topics">
    <li><svg viewBox="0 0 20 20"><circle cx="10" cy="10" r="10" fill="var(--green)"/><path d="M5.5 10.5l3 3 6-6.5" stroke="#fff" stroke-width="2.4" fill="none"/></svg>Vineyard site selection strategies</li>
    <li><svg viewBox="0 0 20 20"><circle cx="10" cy="10" r="10" fill="var(--green)"/><path d="M5.5 10.5l3 3 6-6.5" stroke="#fff" stroke-width="2.4" fill="none"/></svg>Soil analysis</li>
    <li><svg viewBox="0 0 20 20"><circle cx="10" cy="10" r="10" fill="var(--green)"/><path d="M5.5 10.5l3 3 6-6.5" stroke="#fff" stroke-width="2.4" fill="none"/></svg>Irrigation</li>
    <li><svg viewBox="0 0 20 20"><circle cx="10" cy="10" r="10" fill="var(--green)"/><path d="M5.5 10.5l3 3 6-6.5" stroke="#fff" stroke-width="2.4" fill="none"/></svg>Canopy training</li>
    <li><svg viewBox="0 0 20 20"><circle cx="10" cy="10" r="10" fill="var(--green)"/><path d="M5.5 10.5l3 3 6-6.5" stroke="#fff" stroke-width="2.4" fill="none"/></svg>Pest and disease control</li>
    <li><svg viewBox="0 0 20 20"><circle cx="10" cy="10" r="10" fill="var(--green)"/><path d="M5.5 10.5l3 3 6-6.5" stroke="#fff" stroke-width="2.4" fill="none"/></svg>Pruning and trellis basics</li>
    <li><svg viewBox="0 0 20 20"><circle cx="10" cy="10" r="10" fill="var(--green)"/><path d="M5.5 10.5l3 3 6-6.5" stroke="#fff" stroke-width="2.4" fill="none"/></svg>Harvest timing</li>
    <li><svg viewBox="0 0 20 20"><circle cx="10" cy="10" r="10" fill="var(--green)"/><path d="M5.5 10.5l3 3 6-6.5" stroke="#fff" stroke-width="2.4" fill="none"/></svg>Grape varieties</li>
    <li><svg viewBox="0 0 20 20"><circle cx="10" cy="10" r="10" fill="var(--green)"/><path d="M5.5 10.5l3 3 6-6.5" stroke="#fff" stroke-width="2.4" fill="none"/></svg>Working with wineries</li>
    <li><svg viewBox="0 0 20 20"><circle cx="10" cy="10" r="10" fill="var(--green)"/><path d="M5.5 10.5l3 3 6-6.5" stroke="#fff" stroke-width="2.4" fill="none"/></svg>Cost fundamentals</li>
  </ul>

  <p class="abs tagline">INVESTING IN KNOWLEDGE IS<b>INVESTING IN OPPORTUNITIES</b></p>

  <p class="abs location">BROOKVALE</p>

  <section class="abs box schedule">
    <p class="abs day">10 – TUESDAY</p>
    <p class="abs small-cap scholar">LIMITED PARTIAL SCHOLARSHIPS</p>
    <p class="abs evenings">EVENINGS<span>SESSIONS</span></p>
    <div class="abs divider"></div>
    <p class="abs small-cap starting">STARTING</p>
    <p class="abs date"><span class="month">FEB</span><span class="num">28</span></p>
  </section>

  <section class="abs box early">
    <p class="abs early-title">EARLY<br>BIRD<span>SPECIAL</span></p>
    <p class="abs early-note">For those<br>that started<br>or would like<br>to go into<br>viticulture</p>
  </section>
</main>
</body>
</html>
```